BOLD & MINIMALIST DESIGN NEEDED

We want a very bold but minimalistic business card design that is impactful and utilizes both sides of the business card. Our current logo is included for your use.

We want bold fonts and good use of negative space. We don't want the logo to overpower the design.

Target Market(s)

Professionals who are building new commercial buildings.

Industry/Entity Type

Construction

Contact Information for Business Card

Name, Title, email, office phone, cell phone, website

Font styles to use
Serif
Sans Serif

Requirements
Must have
• Bold design!

```html
<!DOCTYPE html>
<html lang="en">
<head>
<meta charset="utf-8">
<title>Ridgeline Design + Build — Business Card</title>
<link rel="stylesheet" href="https://fonts.googleapis.com/css2?family=Poppins:wght@300;400;500;700&display=swap">
<style>
  :root {
    --backdrop: #262626;
    --card: #1e1e1e;
    --card-edge: #2a2a2a;
    --ink-light: #e6e6e6;
    --ink-muted: #bdbdbd;
    --ink-steel: #5a5a5a;
    --accent: #7dc242;
  }
  * { box-sizing: border-box; margin: 0; padding: 0; }
  html, body {
    width: 1200px; height: 576px; overflow: hidden;
    background: var(--backdrop);
    font-family: "Poppins", sans-serif;
  }
  .canvas { position: relative; width: 1200px; height: 576px; }
  .card {
    position: absolute; top: 139px;
    width: 484px; height: 293px;
    border-radius: 8px;
    background: linear-gradient(180deg, var(--card-edge) 0%, var(--card) 60%);
  }
  .card--front { left: 102px; }
  .card--back { left: 597px; }

  .front-wordmark {
    position: absolute; left: 0; right: 0; top: 108px;
    text-align: center;
    font-size: 52px; font-weight: 700; letter-spacing: 2px;
    color: var(--ink-steel);
  }
  .front-url {
    position: absolute; left: 0; right: 0; top: 251px;
    text-align: center;
    font-size: 13px; font-weight: 400; letter-spacing: 7px;
    color: var(--ink-muted);
  }

  .brand {
    position: absolute; left: 50px; top: 125px; width: 170px;
    display: flex; flex-direction: column; align-items: center; gap: 6px;
  }
  .brand-row { display: flex; align-items: center; gap: 8px; }
  .brand-square { width: 14px; height: 14px; background: var(--accent); }
  .brand-name {
    font-size: 22px; font-weight: 700; letter-spacing: 1px;
    color: var(--ink-light);
  }
  .brand-tagline {
    font-size: 10px; font-weight: 500; letter-spacing: 3px;
    color: var(--ink-light);
  }

  .contact { position: absolute; left: 265px; top: 87px; }
  .contact-name { font-size: 20px; font-weight: 500; color: var(--accent); line-height: 1.2; }
  .contact-title { font-size: 12px; font-weight: 400; color: var(--ink-light); margin-top: 2px; }
  .contact-list { list-style: none; margin-top: 22px; }
  .contact-item {
    display: flex; align-items: center; gap: 9px;
    font-size: 12.5px; font-weight: 400; color: var(--ink-light);
    height: 17px;
  }
  .contact-icon { width: 11px; height: 11px; fill: var(--accent); flex: none; }
</style>
</head>
<body>
<main class="canvas">
  <section class="card card--front" aria-label="Card front">
    <p class="front-wordmark">RIDGELINE</p>
    <p class="front-url">www.ridgelinebuild.com</p>
  </section>

  <section class="card card--back" aria-label="Card back">
    <div class="brand">
      <div class="brand-row">
        <span class="brand-square"></span>
        <span class="brand-name">RIDGELINE</span>
      </div>
      <span class="brand-tagline">DESIGN + BUILD</span>
    </div>

    <div class="contact">
      <h1 class="contact-name">Daniel Reyes</h1>
      <p class="contact-title">Director</p>
      <ul class="contact-list">
        <li class="contact-item">
          <svg class="contact-icon" viewBox="0 0 12 12" aria-hidden="true"><path d="M1 4c0-2 2-3 5-3s5 1 5 3v1H8V4H4v1H1z M3 6h6l2 5H1z"/></svg>
          555-014-0127
        </li>
        <li class="contact-item">
          <svg class="contact-icon" viewBox="0 0 12 12" aria-hidden="true"><path d="M0 2h12v8H0z" /><path d="M0 2l6 5 6-5" fill="none" stroke="#1e1e1e" stroke-width="1.2"/></svg>
          dan@ridgelinebuild.com
        </li>
        <li class="contact-item">
          <svg class="contact-icon" viewBox="0 0 12 12" aria-hidden="true"><circle cx="6" cy="6" r="5.5"/><path d="M0.5 6h11M6 0.5v11M2 3h8M2 9h8" stroke="#1e1e1e" stroke-width="0.8" fill="none"/></svg>
          www.ridgelinebuild.com
        </li>
      </ul>
    </div>
  </section>
</main>
</body>
</html>
```